Specialised investor in e-mobility and energy wants business card design

We need a business card design that fits our existing corporate design. <The look and feel must be 'sharp'/'clean', dynamic, communicate momentum, professionalism etc (as one would imagine from a firm in the financial sector). We like the idea of a reverse-side of the card that includes the logo, and the name and contact details on the other. We expect the deliverable to be whatever format might be required to be able to get cards printed directly by a service such as kelmo press. Our website is www.zub.capital

```html
<!DOCTYPE html>
<html lang="en">
<head>
<meta charset="utf-8">
<title>ZUB Capital – Business Card</title>
<link rel="stylesheet" href="https://fonts.googleapis.com/css2?family=Montserrat:wght@400;500;700&display=swap">
<style>
  :root {
    --green-dark: #2f5127;
    --green-light: #7db544;
    --white: #ffffff;
    --stage: #ecefea;
    --ink-soft: rgba(255,255,255,0.92);
  }
  * { margin: 0; padding: 0; box-sizing: border-box; }
  html, body { width: 1200px; height: 960px; overflow: hidden; }
  body {
    background: var(--stage);
    font-family: "Montserrat", Arial, sans-serif;
    position: relative;
  }
  .card {
    position: absolute;
    width: 620px;
    height: 380px;
    border-radius: 30px;
    overflow: hidden;
    box-shadow: 0 6px 18px rgba(0,0,0,0.12);
  }
  .card-front {
    left: 80px; top: 70px;
    background: var(--white);
    display: flex; align-items: center; justify-content: center;
  }
  .front-wordmark {
    color: var(--green-dark);
    font-weight: 500;
    font-size: 78px;
    letter-spacing: 1px;
  }
  .card-back { left: 500px; top: 510px; background: var(--green-dark); }
  .back-shapes { position: absolute; inset: 0; }
  .back-wordmark {
    position: absolute; left: 40px; top: 42px;
    color: var(--white); font-weight: 500; font-size: 34px;
    white-space: nowrap;
  }
  .holder { position: absolute; left: 40px; top: 130px; color: var(--white); white-space: nowrap; }
  .holder-name { font-weight: 700; font-size: 20px; letter-spacing: 1px; text-transform: uppercase; }
  .holder-title { font-weight: 400; font-size: 17px; margin-top: 4px; color: var(--ink-soft); }
  .contact-list { position: absolute; left: 40px; top: 210px; list-style: none; color: var(--white); font-size: 16px; white-space: nowrap; }
  .contact-list li { display: flex; align-items: center; gap: 10px; height: 26px; }
  .contact-list svg { width: 14px; height: 14px; fill: var(--white); }
  .company { position: absolute; left: 40px; top: 306px; color: var(--white); font-size: 16px; line-height: 1.4; white-space: nowrap; }
  .company-name { font-weight: 700; }
  .side-mark {
    position: absolute; left: 425px; top: 118px;
    color: var(--green-dark); font-weight: 700; font-size: 80px; letter-spacing: 2px;
    white-space: nowrap;
  }
</style>
</head>
<body>
  <section class="card card-front" aria-label="Card front">
    <div class="front-wordmark">ZUB Capital</div>
  </section>

  <section class="card card-back" aria-label="Card back">
    <svg class="back-shapes" viewBox="0 0 620 380" width="620" height="380">
      <path d="M340 -20 A330 330 0 0 0 470 380" fill="none" stroke="var(--green-light)" stroke-width="12"/>
      <path d="M356 -20 A318 318 0 0 0 490 380" fill="none" stroke="var(--white)" stroke-width="3"/>
      <circle cx="665" cy="110" r="300" fill="var(--white)"/>
    </svg>
    <div class="back-wordmark">ZUB Capital</div>
    <div class="holder">
      <div class="holder-name">Martin Hallberg</div>
      <div class="holder-title">Managing Director</div>
    </div>
    <ul class="contact-list">
      <li><svg viewBox="0 0 16 16"><path d="M3 1l3 3-2 2c1 2 3 4 5 5l2-2 3 3-2 3C6 14 2 10 1 3z"/></svg>+41 79 555 0148</li>
      <li><svg viewBox="0 0 16 16"><path d="M1 3h14v10H1z M1 3l7 6 7-6" /></svg>martin@zub.capital</li>
      <li><svg viewBox="0 0 16 16"><circle cx="8" cy="8" r="7"/></svg>www.zub.capital</li>
    </ul>
    <div class="company">
      <div class="company-name">ZUB Capital S.A.</div>
      <div>Geneva, Switzerland</div>
    </div>
    <div class="side-mark">ZUB</div>
  </section>
</body>
</html>
```